Re-design and craft the perfect CV platform

We are building a CV-based platform designed to connect employees and employers, with a strong focus on individual users. As we're just starting out, we're looking to have our platform and logo redesigned to better reflect our vision
https://app.zelvorhire.com/
Colors like in the logo attached
#87C032 #6A6E71 #618930 - also you can add more colors if you like.
https://app.zelvorhire.com/dashboard - This page would be nice if you plan it, like personal Bio dashboard. Attached picture (Dashboard wanted) one idea from how we would like to be, but we are open for new professional ideas/solutions.
https://app.zelvorhire.com/posts - On this page we want to be showed the jobs posted. Attached one picture about our idea (jobs page wanted)
https://app.zelvorhire.com/profile - design something nice.
Only Photoshop, Illustrator or Figma
Other pictures from the app attached (as looking right now)

Target Market(s)

Job seekers, HR, Recruiters

Industry/Entity Type

HR Tech

Number of Pages Required

5+ page

Colors
00AB8E
00BBA5
67D7C9
C6EFE9
E9F9F6

```html
<!DOCTYPE html>
<html lang="en">
<head>
<meta charset="utf-8">
<title>Talvenu — Jobs</title>
<link href="https://fonts.googleapis.com/css2?family=Poppins:wght@400;500;600;700&display=swap" rel="stylesheet">
<style>
:root{
  --green:#87C032;
  --green-dark:#618930;
  --grey:#6A6E71;
  --ink:#3a3d40;
  --muted:#5b5f62;
  --band:#ebebec;
  --page:#f5f5f5;
  --card:#ffffff;
  --row:#f6f6f6;
  --row-hi:#f1f7ea;
  --line:#e2e3e4;
}
*{box-sizing:border-box;margin:0;padding:0}
html,body{width:1200px;height:712px;overflow:hidden}
body{font-family:'Poppins',sans-serif;color:var(--ink);background:var(--page);position:relative}
.band{position:absolute;left:0;top:0;width:1200px;height:142px;background:var(--band)}
.brand{position:absolute;left:37px;top:32px;display:flex;align-items:center;gap:7px;white-space:nowrap}
.brand-dot{width:14px;height:14px;border-radius:50%;background:var(--green)}
.brand-name{font-weight:600;font-size:16px;color:var(--green-dark);letter-spacing:.5px}
.head-divider{position:absolute;left:153px;top:19px;width:1px;height:51px;background:#d3d4d5}
.page-title{position:absolute;left:176px;top:31px;font-size:19px;font-weight:600;color:var(--grey);letter-spacing:.5px}
.nav-btn{position:absolute;top:27px;height:33px;width:85px;border:1px solid var(--grey);border-radius:17px;display:flex;align-items:center;justify-content:center;gap:6px;font-size:12px;font-weight:500;color:var(--grey)}
.nav-btn svg{width:12px;height:12px}
.icon-top{position:absolute;top:36px}
.card{position:absolute;top:94px;height:576px;background:var(--card);border-radius:15px}
.profile{left:37px;width:221px}
.jobs{left:280px;width:882px}
.avatar-ring{position:absolute;left:43px;top:22px;width:136px;height:136px;border-radius:50%;border:1px solid var(--green);display:flex;align-items:center;justify-content:center}
.avatar{width:122px;height:122px;border-radius:50%;background:radial-gradient(circle at 50% 40%,#c9a48b 0%,#9b7a66 40%,#b9bcbf 70%)}
.p-name{position:absolute;top:168px;width:100%;text-align:center;font-size:17px;font-weight:600;color:var(--grey)}
.p-mail{position:absolute;top:190px;width:100%;text-align:center;font-size:10.5px;color:var(--muted)}
.facts{position:absolute;left:28px;top:222px;width:180px;display:grid;grid-template-columns:57px 1fr;font-size:10.5px;line-height:20px;white-space:nowrap}
.facts dt{font-weight:600;color:var(--ink)}
.facts dd{color:var(--muted)}
.rule{position:absolute;left:24px;width:172px;height:1px;background:var(--line)}
.block{position:absolute;left:28px;font-size:10.5px;white-space:nowrap}
.block h4{font-weight:600;font-size:11px;margin-bottom:3px}
.block p{color:var(--muted);font-size:10px}
.lang{position:absolute;left:28px;width:165px;font-size:10px;color:var(--muted)}
.lang .row{display:flex;justify-content:space-between}
.bar{margin-top:3px;height:6px;border-radius:3px;background:#e4e5e6;overflow:hidden}
.bar span{display:block;height:100%;background:repeating-linear-gradient(120deg,#2fbf6b 0 6px,#5ad28a 6px 9px);border-radius:3px}
.scroll{position:absolute;width:3px;height:40px;border-radius:2px;background:#e1e2e3}
.search{position:absolute;left:30px;top:30px;width:270px;height:38px;border-radius:19px;background:#f1f1f2;display:flex;align-items:center;justify-content:space-between;padding:0 18px;font-size:10px;color:#8a8d90}
.tool{position:absolute;top:32px;width:34px;height:34px;border-radius:50%;border:1px solid #dcdddd;display:flex;align-items:center;justify-content:center;background:#fff}
.tool.active{background:var(--green);border-color:var(--green)}
.job{position:absolute;left:31px;width:820px;height:83px;border-radius:10px;background:var(--row)}
.job.plain{background:#fff}
.job.hi{background:var(--row-hi);border:1px solid #a7d06e;box-shadow:0 4px 10px rgba(0,0,0,.06)}
.co-logo{position:absolute;left:19px;top:15px;width:53px;height:53px;border-radius:50%;background:#fff;border:1px solid #e3e4e5;display:flex;align-items:center;justify-content:center;font-size:7.5px;font-weight:600;color:var(--grey)}
.co{position:absolute;left:82px;top:25px;font-size:11px;color:var(--muted);white-space:nowrap}
.title{position:absolute;left:82px;top:43px;font-size:12px;font-weight:600;color:var(--ink);white-space:nowrap}
.meta{position:absolute;left:331px;top:30px;font-size:9px;color:var(--muted);line-height:17px;white-space:nowrap}
.meta div{display:flex;align-items:center;gap:5px}
.sal{position:absolute;left:470px;top:25px;font-size:9.5px;color:var(--muted);white-space:nowrap}
.sal b{display:block;font-size:12px;font-weight:500;color:var(--ink);margin-bottom:4px}
.btn{position:absolute;top:27px;width:72px;height:28px;border-radius:14px;font-size:8px;font-weight:600;color:#fff;display:flex;align-items:center;justify-content:center}
.btn.more{left:645px;background:var(--grey)}
.btn.apply{left:729px;background:var(--green)}
</style>
</head>
<body>
<div class="band"></div>

<header>
  <div class="brand"><span class="brand-dot"></span><span class="brand-name">TALVENU</span></div>
  <div class="head-divider"></div>
  <div class="page-title">JOBS</div>
  <div class="nav-btn" style="left:908px"><svg viewBox="0 0 12 12"><rect x="1" y="3" width="10" height="7" rx="1" fill="#87C032"/><rect x="4" y="1" width="4" height="3" rx="1" fill="none" stroke="#87C032"/></svg>Jobs</div>
  <div class="nav-btn" style="left:1001px"><svg viewBox="0 0 12 12"><path d="M2 1h5l3 3v7H2z" fill="#87C032"/></svg>CV</div>
  <svg class="icon-top" style="left:1108px" width="18" height="18" viewBox="0 0 18 18"><path d="M9 2a5 5 0 0 0-5 5v4l-2 2h14l-2-2V7a5 5 0 0 0-5-5z" fill="#6A6E71"/><circle cx="9" cy="15.5" r="1.6" fill="#6A6E71"/><circle cx="14" cy="3" r="2.3" fill="#e53935"/></svg>
  <svg class="icon-top" style="left:1146px" width="18" height="18" viewBox="0 0 18 18"><circle cx="7" cy="5" r="3.5" fill="#6A6E71"/><path d="M1 15c0-3.5 2.7-5.5 6-5.5 1.5 0 2.8.4 3.8 1.1L8 15z" fill="#6A6E71"/><path d="M11 15l5-5 1.5 1.5-5 5H11z" fill="#6A6E71"/></svg>
</header>

<aside class="card profile">
  <div class="avatar-ring"><div class="avatar" role="img" aria-label="Profile photo of the candidate"></div></div>
  <div class="p-name">Dario Feltz</div>
  <div class="p-mail">info@dariofeltz.com</div>
  <dl class="facts">
    <dt>Phone:</dt><dd>+08 555 201 4417</dd>
    <dt>Age:</dt><dd>30</dd>
    <dt>Gender:</dt><dd>Male</dd>
  </dl>
  <div class="rule" style="top:288px"></div>
  <div class="block" style="top:302px"><h4>Field of Expertise (Szakmaja):</h4><p>Software Development</p></div>
  <div class="rule" style="top:346px"></div>
  <div class="block" style="top:359px"><h4>Highest Level of Education:</h4><p>Master's in Computer Science</p></div>
  <div class="rule" style="top:411px"></div>
  <div class="block" style="top:430px"><h4>Languages:</h4></div>
  <div class="lang" style="top:456px"><div class="row"><span>Romanian:</span><span>65%</span></div><div class="bar"><span style="width:57%"></span></div></div>
  <div class="lang" style="top:491px"><div class="row"><span>Hungarian</span><span>100%</span></div><div class="bar"><span style="width:100%"></span></div></div>
  <div class="lang" style="top:526px"><div class="row"><span>English</span><span>80%</span></div><div class="bar"><span style="width:82%"></span></div></div>
  <div class="scroll" style="left:211px;top:390px"></div>
</aside>

<main class="card jobs">
  <div class="search"><span>Enter filter keyword</span>
    <svg width="14" height="14" viewBox="0 0 14 14"><circle cx="6" cy="6" r="4.5" fill="none" stroke="#4a4d50" stroke-width="1.6"/><path d="M9.5 9.5L13 13" stroke="#4a4d50" stroke-width="1.6" stroke-linecap="round"/></svg></div>

  <div class="tool" style="left:659px"><svg width="14" height="14" viewBox="0 0 14 14" fill="none" stroke="#6A6E71" stroke-width="1.3"><rect x="1" y="1" width="5" height="5" rx="1"/><rect x="8" y="1" width="5" height="5" rx="1"/><rect x="1" y="8" width="5" height="5" rx="1"/><rect x="8" y="8" width="5" height="5" rx="1"/></svg></div>
  <div class="tool active" style="left:699px"><svg width="16" height="14" viewBox="0 0 16 14" fill="none" stroke="#fff" stroke-width="1.6" stroke-linecap="round"><path d="M1 2h11M1 6h11M1 10h5M9 10l2 2 4-4"/></svg></div>
  <div class="tool" style="left:739px"><svg width="14" height="14" viewBox="0 0 14 14"><path d="M1 1.5h12L8.5 7v5l-3-1.5V7z" fill="none" stroke="#6A6E71" stroke-width="1.3" stroke-linejoin="round"/></svg></div>
  <div class="tool" style="left:778px"><svg width="14" height="14" viewBox="0 0 14 14"><path d="M12 7a5 5 0 1 1-1.5-3.6" fill="none" stroke="#4a4d50" stroke-width="1.8"/><path d="M11.5 1v3.5H8" fill="none" stroke="#4a4d50" stroke-width="1.8"/></svg></div>
  <div class="tool" style="left:818px"><svg width="4" height="14" viewBox="0 0 4 14" fill="#4a4d50"><circle cx="2" cy="2" r="1.5"/><circle cx="2" cy="7" r="1.5"/><circle cx="2" cy="12" r="1.5"/></svg></div>

  <div class="job" style="top:105px">
    <div class="co-logo">Norvane</div>
    <div class="co">Norvane Systems</div><div class="title">Full Stack Developer E-commerce</div>
    <div class="meta"><div><svg width="8" height="9" viewBox="0 0 8 10"><path d="M4 0a3.5 3.5 0 0 0-3.5 3.5C.5 6 4 10 4 10s3.5-4 3.5-6.5A3.5 3.5 0 0 0 4 0z" fill="#4a4d50"/><circle cx="4" cy="3.5" r="1.2" fill="#fff"/></svg>Seattle, USA</div><div><svg width="8" height="8" viewBox="0 0 8 8"><circle cx="4" cy="4" r="4" fill="#4a4d50"/><path d="M4 2v2.2h1.6" stroke="#fff" fill="none"/></svg>Full-time</div></div>
    <div class="sal"><b>Salary</b>€60,000 - €75,000 per year</div>
    <div class="btn more">VIEW MORE</div><div class="btn apply">APPLY</div>
  </div>

  <div class="job plain" style="top:188px">
    <div class="co-logo">Quillstone</div>
    <div class="co">Quillstone Capital</div><div class="title">Product Manager - FinTech</div>
    <div class="meta"><div><svg width="8" height="9" viewBox="0 0 8 10"><path d="M4 0a3.5 3.5 0 0 0-3.5 3.5C.5 6 4 10 4 10s3.5-4 3.5-6.5A3.5 3.5 0 0 0 4 0z" fill="#4a4d50"/><circle cx="4" cy="3.5" r="1.2" fill="#fff"/></svg>London, UK</div><div><svg width="8" height="8" viewBox="0 0 8 8"><circle cx="4" cy="4" r="4" fill="#4a4d50"/><path d="M4 2v2.2h1.6" stroke="#fff" fill="none"/></svg>Part-time</div></div>
    <div class="sal"><b>Salary</b>£45,000 - £60,000 per year</div>
    <div class="btn more">VIEW MORE</div><div class="btn apply">APPLY</div>
  </div>

  <div class="job hi" style="top:271px">
    <div class="co-logo" style="top:14px;left:18px">Brightfold</div>
    <div class="co" style="top:24px;left:81px">Brightfold Analytics</div><div class="title" style="top:42px;left:81px">Data Engineer Analytics Platform</div>
    <div class="meta" style="left:330px;top:29px"><div><svg width="8" height="9" viewBox="0 0 8 10"><path d="M4 0a3.5 3.5 0 0 0-3.5 3.5C.5 6 4 10 4 10s3.5-4 3.5-6.5A3.5 3.5 0 0 0 4 0z" fill="#4a4d50"/><circle cx="4" cy="3.5" r="1.2" fill="#fff"/></svg>Dublin, Ireland</div><div><svg width="8" height="8" viewBox="0 0 8 8"><circle cx="4" cy="4" r="4" fill="#4a4d50"/><path d="M4 2v2.2h1.6" stroke="#fff" fill="none"/></svg>Full-time</div></div>
    <div class="sal" style="left:469px;top:24px"><b>Salary</b>€55,000 - €70,000 per year</div>
    <div class="btn more" style="left:644px;top:26px">VIEW MORE</div><div class="btn apply" style="left:728px;top:26px">APPLY</div>
  </div>

  <div class="job plain" style="top:354px">
    <div class="co-logo">Lumora</div>
    <div class="co">Lumora Labs</div><div class="title">UX/UI Designer - SaaS Product</div>
    <div class="meta"><div><svg width="8" height="9" viewBox="0 0 8 10"><path d="M4 0a3.5 3.5 0 0 0-3.5 3.5C.5 6 4 10 4 10s3.5-4 3.5-6.5A3.5 3.5 0 0 0 4 0z" fill="#4a4d50"/><circle cx="4" cy="3.5" r="1.2" fill="#fff"/></svg>Remote</div><div><svg width="8" height="8" viewBox="0 0 8 8"><circle cx="4" cy="4" r="4" fill="#4a4d50"/><path d="M4 2v2.2h1.6" stroke="#fff" fill="none"/></svg>Full-time</div></div>
    <div class="sal"><b>Salary</b>$50 - $70 per hour</div>
    <div class="btn more">VIEW MORE</div><div class="btn apply">APPLY</div>
  </div>

  <div class="job" style="top:437px">
    <div class="co-logo">Skyvell</div>
    <div class="co">Skyvell</div><div class="title">Backend Developer - Cloud</div>
    <div class="meta"><div><svg width="8" height="9" viewBox="0 0 8 10"><path d="M4 0a3.5 3.5 0 0 0-3.5 3.5C.5 6 4 10 4 10s3.5-4 3.5-6.5A3.5 3.5 0 0 0 4 0z" fill="#4a4d50"/><circle cx="4" cy="3.5" r="1.2" fill="#fff"/></svg>Seattle, USA</div><div><svg width="8" height="8" viewBox="0 0 8 8"><circle cx="4" cy="4" r="4" fill="#4a4d50"/><path d="M4 2v2.2h1.6" stroke="#fff" fill="none"/></svg>Full-time</div></div>
    <div class="sal"><b>Salary</b>$80,000 - $100,000 per year</div>
    <div class="btn more">VIEW MORE</div><div class="btn apply">APPLY</div>
  </div>

  <div class="scroll" style="left:870px;top:391px"></div>
</main>
</body>
</html>
```